Car rental website design for a UAE car rental company

This project is about creating a new website design for a car rental company located in Dubai (United Arab Emirates), I opened the same project a few months ago but I didn't receive a lot of appealing entries so I closed it but this time I am marking the project as guaranteed to avoid such situation again, if you have already provided a design before then please re-submit again on this project so that it is considered while reviewing all the designs

A few important things:

1- We need a simple non-complex design
2- The final deliverable would be 2 screens (PSD, JPEG ... etc), the first screen is for the home page and the second screen is for an internal page
3- The home page must have a section that end users can use to rent a car online directly from the home page instead of going into some inner pages
4- The current website is very old and not very appealing so avoid creating a similar design (www.crestvane-autos.example)
5- The name is Crestvane but the company rents normal cars (no Limousin cars will be rented) so avoid adding any fancy cars in the images/graphics used in the design, just normal end users cars
6- The expected pages would be: home, About us, Our team, Strategy, Contact us and links to social media pages
7- The attachments include the company's logo and some screens from other car rental companies that provide online rentals/payments

If you have any questions please feel free to ask and please note that we will need the designs urgently

Thanks

Target Market(s)

Dubai - United Arab Emirates

Industry/Entity Type

It Company

Number of Pages Required

2 page

Font styles to use
Sans Serif

Requirements
Must have
• Check the project details
Nice to have
Should not have

```html
<!DOCTYPE html>
<html lang="en">
<head>
<meta charset="utf-8">
<title>Crestvane Rent A Car</title>
<link rel="stylesheet" href="https://fonts.googleapis.com/css2?family=Open+Sans:wght@400;600;700&family=Jost:wght@300;400;500&family=Great+Vibes&display=swap">
<style>
  :root {
    --accent: #a3104a;
    --accent-dark: #8e0a3e;
    --ink: #3c3c3c;
    --muted: #6a6a6a;
    --hero-bg: #c3cdc7;
    --hero-stripe: #bac5bf;
    --panel-top: #808f87;
    --panel-bottom: #5c6a62;
    --panel-rim: #dfe5e2;
    --field: #f3f3f3;
    --field-line: #c8c8c8;
    --white: #ffffff;
    --social: #6f8a9a;
    --car-light: #e2463f;
    --car-mid: #c92824;
    --car-shade: #b7c2bc;
  }
  * { box-sizing: border-box; margin: 0; padding: 0; }
  html, body { width: 1200px; height: 858px; overflow: hidden; background: var(--white); }
  body { position: relative; font-family: "Open Sans", Arial, sans-serif; color: var(--ink); }

  /* Header */
  .site-header { position: absolute; left: 0; top: 0; width: 1200px; height: 102px; background: var(--white); }
  .brand { position: absolute; left: 96px; top: 36px; display: flex; align-items: center; gap: 10px; }
  .brand-square { width: 26px; height: 26px; background: var(--accent); }
  .brand-name { font-size: 24px; font-weight: 600; color: var(--accent); }
  .main-nav { position: absolute; top: 43px; left: 376px; }
  .main-nav a { position: absolute; white-space: nowrap; font-family: "Jost", sans-serif; font-size: 15px; font-weight: 400; color: #555; text-decoration: none; }
  .main-nav a.is-active { color: var(--accent); }
  .main-nav a.is-active::after { content: ""; position: absolute; left: 0; right: 0; bottom: -7px; height: 2px; background: var(--accent); }
  .account-links { position: absolute; right: 74px; top: 10px; font-size: 11px; color: #666; letter-spacing: .3px; }
  .social { display: flex; gap: 5px; position: absolute; }
  .social span { width: 24px; height: 24px; border-radius: 50%; background: var(--social); }
  .site-header .social { right: 74px; top: 40px; }

  /* Hero */
  .hero { position: absolute; left: 0; top: 102px; width: 1200px; height: 672px;
    background: repeating-linear-gradient(90deg, var(--hero-bg) 0 3px, var(--hero-stripe) 3px 4px); }
  .hero-title { position: absolute; left: 74px; top: 44px; display: flex; align-items: baseline; gap: 16px; font-weight: 400; }
  .hero-title .script { font-family: "Great Vibes", cursive; font-weight: 400; font-size: 76px; color: #1d1d1d; line-height: 1; }
  .hero-title .tag { font-family: "Jost", sans-serif; font-weight: 400; font-size: 24px; color: #222; }
  .hero-lead { position: absolute; left: 74px; top: 180px; width: 480px; font-family: "Jost", sans-serif; font-weight: 300;
    font-size: 17px; line-height: 24px; color: var(--white); text-transform: uppercase; }
  .hero-car { position: absolute; left: 72px; top: 300px; width: 600px; height: 294px; border-radius: 14px;
    background: radial-gradient(ellipse 60% 55% at 48% 48%, var(--car-light) 0%, var(--car-mid) 60%, var(--car-shade) 100%); }

  /* Booking panel */
  .booking-rim { position: absolute; left: 686px; top: 40px; width: 440px; height: 592px; border-radius: 28px; background: var(--panel-rim); }
  .booking { position: absolute; left: 696px; top: 48px; width: 420px; height: 576px; border-radius: 22px;
    background: linear-gradient(180deg, var(--panel-top), var(--panel-bottom)); color: var(--white); }
  .booking > * { position: absolute; }
  .booking h2 { left: 32px; top: 24px; font-family: "Jost", sans-serif; font-weight: 500; font-size: 29px; letter-spacing: .5px; }
  .booking .rule { left: 32px; top: 70px; width: 66px; height: 1px; background: rgba(255,255,255,.7); }
  .step { width: 34px; height: 40px; background: var(--white); border: 1px solid var(--accent); outline: 2px solid var(--white);
    color: var(--accent); font-family: "Jost", sans-serif; font-size: 20px; display: flex; align-items: center; justify-content: center; left: 34px; }
  .label { left: 82px; font-family: "Jost", sans-serif; font-size: 15px; font-weight: 500; white-space: nowrap; }
  .label small { font-family: "Open Sans", sans-serif; font-size: 11px; font-weight: 400; }
  .note { left: 82px; font-size: 11px; white-space: nowrap; }
  .field { left: 82px; height: 32px; border-radius: 3px; background: linear-gradient(#ffffff, #e6e6e6); border: 1px solid var(--field-line);
    color: #666; font-size: 11.5px; display: flex; align-items: center; justify-content: space-between; padding: 0 12px; }
  .check { left: 82px; display: flex; align-items: center; gap: 8px; font-size: 11.5px; white-space: nowrap; }
  .check i { width: 11px; height: 11px; background: var(--field); border: 1px solid #aaa; }
  .help { display: inline-flex; width: 17px; height: 17px; border-radius: 50%; background: #a7b1ab; color: var(--white);
    font-size: 11px; font-weight: 700; align-items: center; justify-content: center; font-style: normal; }
  .quote-btn { left: 82px; top: 494px; width: 304px; height: 39px; background: var(--accent); border-radius: 2px;
    font-family: "Jost", sans-serif; font-size: 15px; font-weight: 500; display: flex; align-items: center; justify-content: center; }
  .manage { left: 82px; top: 541px; width: 304px; text-align: center; font-size: 10.5px; color: #111; font-family: "Jost", sans-serif; }

  /* Footer */
  .site-footer { position: absolute; left: 0; top: 774px; width: 1200px; height: 84px; background: var(--white); }
  .news-icon { position: absolute; left: 74px; top: 26px; }
  .news-text { position: absolute; left: 145px; top: 24px; white-space: nowrap; }
  .news-text strong { display: block; font-family: "Jost", sans-serif; font-size: 13.5px; font-weight: 500; color: #222; line-height: 18px; }
  .news-text span { display: block; font-size: 11.5px; color: #555; line-height: 17px; }
  .news-form { position: absolute; left: 456px; top: 25px; display: flex; height: 31px; }
  .news-form .email { width: 237px; border: 1px solid #bbb; border-right: 0; font-size: 12px; color: #666; padding: 0 11px; display: flex; align-items: center; }
  .news-form .submit { width: 74px; background: var(--accent-dark); color: var(--white); font-size: 12px; display: flex; align-items: center; justify-content: center; }
  .site-footer .social { right: 74px; top: 18px; }
  .copyright { position: absolute; right: 74px; top: 50px; font-size: 12px; color: #444; }
</style>
</head>
<body>
  <header class="site-header">
    <div class="brand"><span class="brand-square"></span><span class="brand-name">Crestvane</span></div>
    <nav class="main-nav">
      <a class="is-active" href="#" style="left:0">HOME</a>
      <a href="#" style="left:72px">ABOUT US</a>
      <a href="#" style="left:168px">OUR TEAM</a>
      <a href="#" style="left:268px">STRATEGY</a>
      <a href="#" style="left:362px">CONTACT US</a>
    </nav>
    <div class="account-links">LOGIN &nbsp;|&nbsp; REGISTER</div>
    <div class="social" aria-label="Social media links"><span></span><span></span><span></span><span></span><span></span></div>
  </header>

  <section class="hero">
    <h1 class="hero-title"><span class="script">Crestvane</span><span class="tag">RENT A CAR</span></h1>
    <p class="hero-lead">As Dubai is expected to welcome millions of tourists and visitors, car rental industry is believed to escalate more rapidly in the region.</p>
    <div class="hero-car" role="img" aria-label="Photo of a red family sedan"></div>

    <div class="booking-rim"></div>
    <form class="booking">
      <h2>BOOK A CAR</h2>
      <div class="rule"></div>

      <div class="step" style="top:96px">01</div>
      <div class="label" style="top:94px">PICK-UP LOCATION <small>(City,State or Airport Code)</small></div>
      <div class="note" style="top:118px">Previous Searches</div>
      <div class="field" style="top:140px;width:304px"></div>
      <div class="note" style="top:179px">Help me find a rental location</div>
      <div class="check" style="top:201px"><i></i>Return car to different Crestvane location <em class="help">?</em></div>

      <div class="step" style="top:240px">02</div>
      <div class="label" style="top:240px">PICK-UP DATE AND TIME:</div>
      <div class="field" style="top:266px;width:146px">DD/MM/YY
        <svg width="12" height="12" viewBox="0 0 12 12"><rect x="1" y="2" width="10" height="9" fill="none" stroke="#888"/><line x1="1" y1="5" x2="11" y2="5" stroke="#888"/></svg></div>
      <div class="field" style="top:266px;left:239px;width:147px">HH:MM
        <svg width="8" height="12" viewBox="0 0 8 12"><path d="M1 5 4 1 7 5ZM1 7 4 11 7 7Z" fill="#888"/></svg></div>

      <div class="label" style="top:311px">RETURN DATE AND TIME:</div>
      <div class="field" style="top:336px;width:146px">DD/MM/YY
        <svg width="12" height="12" viewBox="0 0 12 12"><rect x="1" y="2" width="10" height="9" fill="none" stroke="#888"/><line x1="1" y1="5" x2="11" y2="5" stroke="#888"/></svg></div>
      <div class="field" style="top:336px;left:239px;width:147px">HH:MM
        <svg width="8" height="12" viewBox="0 0 8 12"><path d="M1 5 4 1 7 5ZM1 7 4 11 7 7Z" fill="#888"/></svg></div>

      <div class="label" style="top:388px">HIRE CAR TYPE: <em class="help">?</em></div>
      <div class="field" style="top:416px;width:304px">Show Me All
        <svg width="14" height="8" viewBox="0 0 14 8"><path d="M1 1 7 7 13 1" fill="none" stroke="#777" stroke-width="1.4"/></svg></div>
      <div class="check" style="top:459px"><i></i>Apply a discount code <em class="help">?</em></div>

      <div class="quote-btn">GET A QUOTE</div>
      <div class="manage">VIEW/MODIFY/CANCEL A RESERVATION</div>
    </form>
  </section>

  <footer class="site-footer">
    <svg class="news-icon" width="60" height="28" viewBox="0 0 60 28" aria-hidden="true">
      <rect x="22" y="4" width="34" height="22" fill="none" stroke="#999" stroke-width="1.5"/>
      <path d="M22 4 39 17 56 4" fill="none" stroke="#999" stroke-width="1.5"/>
      <line x1="2" y1="10" x2="18" y2="10" stroke="#bbb"/><line x1="6" y1="16" x2="18" y2="16" stroke="#bbb"/><line x1="10" y1="22" x2="18" y2="22" stroke="#bbb"/>
    </svg>
    <div class="news-text"><strong>SIGN UP TO CRESTVANE EMAIL NEWSLETTER</strong><span>Enter your email &amp; give me latest news &amp; updates</span></div>
    <div class="news-form"><div class="email">Enter your email</div><div class="submit">SIGN UP</div></div>
    <div class="social" aria-label="Social media links"><span></span><span></span><span></span><span></span><span></span></div>
    <div class="copyright">©2015 Crestvane. All Rights Reserved.</div>
  </footer>
</body>
</html>
```